Banner Design 4040mm W x 2190mm H

Design a glamorous and exciting 4040mm W x 2190mm H backdrop for the QLMRT Velvet Harbour Gala at the luxurious Tamsin Hall, Vellora, Whitcombe Quay, Sydney. This exciting backdrop should be spectacular so that people will be excited to take photos in front of it.
Design Colours preferred is black and pink.
Please include our website on the banner www.qlmrt.org.au
Should include the words "QLMRT Velvet Harbour Gala" as the main attraction on the banner.
Please include "Thank you to our sponsors" and include the logo of the sponsors.
Sponsors:
Brenwick Pathology
NorthGlen Radiology
KTV Diagnostic Imaging
Harbin Legal Partners
Denhams
Banner Template:
4040mm W x 2190mm H Single Sided (.AI)
https://files.examplestore.net/d/8Rk2mZpQ7vLx3TnW5yBc/view
QLMRT Logo:
Can be obtained from our website www.qlmrt.org.au

```html
<!DOCTYPE html>
<html lang="en">
<head>
<meta charset="utf-8">
<title>QLMRT Velvet Harbour Gala – Backdrop</title>
<link rel="stylesheet" href="https://fonts.googleapis.com/css2?family=Montserrat:wght@600;800&family=Kaushan+Script&family=Michroma&display=swap">
<style>
  :root {
    --page: #dcdcdc;
    --night: #12030f;
    --plum: #3a0630;
    --neon-pink: #ff2fd6;
    --white: #ffffff;
    --soft-white: rgba(255, 255, 255, 0.85);
    --panel: rgba(6, 0, 6, 0.82);
    --sponsor-blue: #2a73c4;
    --sponsor-red: #ff2f6e;
    --sponsor-violet: #8e67e6;
    --sponsor-gold: #e9b92b;
  }
  * { margin: 0; padding: 0; box-sizing: border-box; }
  html, body { width: 889px; height: 1200px; overflow: hidden; }
  body { background: var(--page); position: relative; }

  .backdrop {
    position: absolute;
    left: 34px; top: 378px;
    width: 820px; height: 444px;
    overflow: hidden;
    background: var(--night);
    box-shadow: 0 8px 18px rgba(0,0,0,0.45);
  }
  .backdrop__wall {
    position: absolute; inset: 0;
    background:
      radial-gradient(ellipse 38% 55% at 50% 38%, rgba(60,80,200,0.75), rgba(40,20,90,0.2) 70%, transparent),
      linear-gradient(180deg, var(--plum) 0%, var(--night) 55%, #1a0418 100%);
  }
  .backdrop__wings {
    position: absolute;
    left: 70px; top: 40px; width: 680px; height: 290px;
    background:
      radial-gradient(ellipse 30% 60% at 30% 55%, rgba(255,47,214,0.55), transparent 70%),
      radial-gradient(ellipse 30% 60% at 70% 55%, rgba(255,47,214,0.55), transparent 70%);
    filter: blur(4px);
  }
  .backdrop__floor {
    position: absolute; left: 0; right: 0; bottom: 0; height: 50px;
    background: radial-gradient(ellipse 50% 90% at 50% 100%, rgba(255,47,214,0.55), transparent 75%);
  }
  .client-mark {
    position: absolute; left: 66px; top: 40px;
    display: flex; align-items: center; gap: 6px;
    font-family: "Montserrat", sans-serif; font-weight: 600;
    font-size: 15px; color: var(--white); letter-spacing: 1px;
  }
  .client-mark__dot { width: 12px; height: 12px; background: var(--white); border-radius: 50%; }

  .event-acronym {
    position: absolute; left: 0; right: 0; top: 40px;
    text-align: center;
    font-family: "Montserrat", sans-serif; font-weight: 800;
    font-size: 128px; line-height: 1; letter-spacing: 2px;
    color: var(--neon-pink);
    text-shadow: 0 0 18px rgba(255,47,214,0.8);
  }
  .event-name {
    position: absolute; left: 0; right: 0; top: 168px;
    text-align: center;
    font-family: "Kaushan Script", cursive;
    font-size: 78px; line-height: 1.1;
    color: var(--white);
    text-shadow: 0 3px 6px rgba(0,0,0,0.6);
  }
  .sponsors {
    position: absolute; left: 50px; top: 290px;
    width: 720px; height: 96px;
    background: var(--panel);
    border-radius: 16px;
  }
  .sponsors__heading {
    margin-top: 8px; text-align: center;
    font-family: "Michroma", sans-serif;
    font-size: 15px; letter-spacing: 6px; color: var(--white);
  }
  .sponsors__list {
    list-style: none;
    display: flex; justify-content: space-between; align-items: center;
    padding: 12px 24px 0;
    font-family: "Montserrat", sans-serif; font-weight: 600;
    font-size: 14px; line-height: 1.2;
  }
  .sponsor {
    width: 118px;
    display: flex; align-items: center; justify-content: center; gap: 6px;
    text-align: center;
  }
  .sponsor__square { flex: none; width: 12px; height: 12px; }
  .sponsor--denhams { color: var(--sponsor-blue); }
  .sponsor--denhams .sponsor__square { background: var(--sponsor-blue); }
  .sponsor--brenwick { color: var(--sponsor-red); }
  .sponsor--ktv { color: var(--sponsor-violet); }
  .sponsor--northglen { color: var(--white); }
  .sponsor--harbin { color: var(--sponsor-gold); }

  .website {
    position: absolute; left: 0; right: 0; top: 398px;
    text-align: center;
    font-family: "Michroma", sans-serif;
    font-size: 11px; letter-spacing: 3px;
    color: var(--soft-white);
  }
</style>
</head>
<body>
  <section class="backdrop">
    <div class="backdrop__wall" role="img" aria-label="Dark brick wall lit in blue and magenta"></div>
    <div class="backdrop__wings" role="img" aria-label="Glowing neon pink angel wings"></div>
    <div class="backdrop__floor" role="img" aria-label="Pink neon glow reflected on the floor"></div>

    <div class="client-mark"><span class="client-mark__dot"></span>QLMRT</div>

    <h1 class="event-acronym">QLMRT</h1>
    <h2 class="event-name">Velvet Harbour Gala</h2>

    <div class="sponsors">
      <p class="sponsors__heading">THANK YOU TO OUR SPONSORS</p>
      <ul class="sponsors__list">
        <li class="sponsor sponsor--denhams"><span class="sponsor__square"></span>Denhams</li>
        <li class="sponsor sponsor--brenwick">Brenwick<br>Pathology</li>
        <li class="sponsor sponsor--ktv">KTV Diagnostic<br>Imaging</li>
        <li class="sponsor sponsor--northglen">NorthGlen<br>Radiology</li>
        <li class="sponsor sponsor--harbin">Harbin Legal<br>Partners</li>
      </ul>
    </div>

    <p class="website">www.qlmrt.org.au</p>
  </section>
</body>
</html>
```